OBK Farcoast Logistics Limited

We need the buissnes card to be very exclusive. As we are all young in our company. We need this to be the gate to make our clients feel deep interest for us.

We are focused in as International Trade advisors, and our products go from Oil Tanker Ships to Rubber balls for dogs.

Our Slogan is Bringing Far Close.
And our main marketing will be through Internet.

We were stablished in 2009 In Mexico and we also have offices in Hong Kong.
We have representatives in China and Europe.

Target Market(s)

Is every company or Individual that wants to develop an International Project or product development or Logistic service of Goods and people.
Some of our current projects are Ship Brokerage, Mine Brokerage, Real State and Product Pormotional development.

Industry/Entity Type

It Company

Requirements
Must have
• Our Logo and slogan, and make the card accoriding to the logo.
Nice to have
• Our Colors

```html
<!DOCTYPE html>
<html lang="en">
<head>
<meta charset="utf-8">
<title>OBK Farcoast Logistics Limited – Business Card</title>
<link href="https://fonts.googleapis.com/css2?family=Open+Sans:wght@400;600;700&display=swap" rel="stylesheet">
<style>
  :root {
    --stage: #e9e6e1;
    --card-black: #1d1d1f;
    --brand-green: #8dc63f;
    --brand-blue: #29abe2;
    --deep-blue: #1f5fa8;
    --text-light: #f2f2f2;
    --text-dark: #1d1d1f;
    --divider: #8a8a8a;
  }
  * { box-sizing: border-box; margin: 0; padding: 0; }
  html, body { width: 1200px; height: 720px; overflow: hidden; }
  body {
    background: var(--stage);
    font-family: "Open Sans", Arial, sans-serif;
    display: flex;
    align-items: center;
    justify-content: center;
    gap: 40px;
  }
  .card {
    position: relative;
    width: 560px;
    height: 320px;
    background: var(--card-black);
    overflow: hidden;
    box-shadow: 0 6px 18px rgba(0,0,0,0.18);
  }

  /* Front face */
  .card-wave { position: absolute; inset: 0; width: 100%; height: 100%; }
  .brand-block {
    position: absolute;
    left: 40px;
    top: 40px;
    width: 180px;
    display: flex;
    flex-direction: column;
    align-items: center;
  }
  .brand-dot {
    width: 64px; height: 64px;
    border-radius: 50%;
    background: var(--brand-blue);
  }
  .brand-name {
    margin-top: 10px;
    color: var(--brand-green);
    font-weight: 700;
    font-size: 40px;
    letter-spacing: 2px;
    line-height: 1;
  }
  .brand-slogan {
    margin-top: 6px;
    color: var(--brand-blue);
    font-size: 10px;
    letter-spacing: 0.3px;
  }
  .divider {
    position: absolute;
    left: 250px;
    top: 40px;
    width: 2px;
    height: 112px;
    background: linear-gradient(to bottom, transparent, var(--divider), transparent);
    transform: rotate(10deg);
  }
  .contact-block {
    position: absolute;
    left: 272px;
    top: 30px;
    color: var(--text-light);
  }
  .person-name {
    color: var(--brand-green);
    font-weight: 700;
    font-size: 17px;
    line-height: 1.2;
  }
  .person-role {
    color: var(--brand-blue);
    font-size: 12px;
    margin-bottom: 8px;
  }
  .contact-list { list-style: none; }
  .contact-list li {
    display: flex;
    align-items: center;
    gap: 9px;
    font-size: 12.5px;
    line-height: 20px;
  }
  .contact-icon { width: 12px; height: 12px; flex: none; }
  .address {
    position: absolute;
    left: 0; right: 0;
    bottom: 30px;
    text-align: center;
    color: var(--text-dark);
    font-size: 14px;
    letter-spacing: 0.6px;
    transform: rotate(-5deg);
    transform-origin: center;
  }

  /* Back face */
  .back-mark {
    position: absolute;
    left: 0; right: 0;
    top: 78px;
    display: flex;
    align-items: center;
    justify-content: center;
    gap: 18px;
  }
  .back-mark .brand-dot { width: 40px; height: 40px; }
  .back-mark .brand-name { margin-top: 0; font-size: 84px; letter-spacing: 4px; }
  .back-url {
    position: absolute;
    left: 0; right: 0;
    bottom: 40px;
    text-align: center;
    color: var(--text-light);
    font-size: 17px;
    letter-spacing: 3px;
  }
  .back-url .url-domain { color: var(--brand-blue); }
</style>
</head>
<body>

  <section class="card card-front" aria-label="Business card front">
    <svg class="card-wave" viewBox="0 0 560 320" preserveAspectRatio="none" aria-hidden="true">
      <path d="M0 262 C160 252 340 214 560 122 L560 320 L0 320 Z" fill="#8dc63f"/>
      <path d="M0 257 C160 247 340 208 560 116" fill="none" stroke="#29abe2" stroke-width="5"/>
      <path d="M0 252 C160 242 340 200 560 108" fill="none" stroke="#1f5fa8" stroke-width="1.5"/>
    </svg>

    <div class="brand-block">
      <span class="brand-dot"></span>
      <span class="brand-name">OBK</span>
      <p class="brand-slogan">Bringing Far Close</p>
    </div>

    <div class="divider"></div>

    <div class="contact-block">
      <p class="person-name">Your Name</p>
      <p class="person-role">Position</p>
      <ul class="contact-list">
        <li>
          <svg class="contact-icon" viewBox="0 0 12 12"><circle cx="6" cy="6" r="5.5" fill="none" stroke="#f2f2f2"/><path d="M4 3.5 L5 3.5 L5.6 5 L5 5.6 Q5.6 6.8 6.6 7.2 L7.2 6.6 L8.6 7.2 L8.6 8.2 Q6.5 8.6 4.8 6.9 Q3.6 5.6 4 3.5 Z" fill="#f2f2f2"/></svg>
          123-456-7890
        </li>
        <li>
          <svg class="contact-icon" viewBox="0 0 12 12"><rect x="2" y="3" width="8" height="6" rx="1" fill="#f2f2f2"/><rect x="3.5" y="4.5" width="5" height="2" fill="#1d1d1f"/></svg>
          123-456-7890
        </li>
        <li>
          <svg class="contact-icon" viewBox="0 0 12 12"><rect x="1" y="3" width="10" height="7" rx="1" fill="#f2f2f2"/><path d="M1.5 3.5 L6 7 L10.5 3.5" fill="none" stroke="#1d1d1f"/></svg>
          info@farcoast.example
        </li>
        <li>
          <svg class="contact-icon" viewBox="0 0 12 12"><circle cx="6" cy="6" r="5" fill="none" stroke="#f2f2f2"/><ellipse cx="6" cy="6" rx="2.2" ry="5" fill="none" stroke="#f2f2f2"/><path d="M1 6 H11" stroke="#f2f2f2"/></svg>
          www.farcoast.example
        </li>
      </ul>
    </div>

    <p class="address">00, Complex Name, City, State, 00045</p>
  </section>

  <section class="card card-back" aria-label="Business card back">
    <div class="back-mark">
      <span class="brand-dot"></span>
      <span class="brand-name">OBK</span>
    </div>
    <p class="back-url">www.<span class="url-domain">farcoast</span>.example</p>
  </section>

</body>
</html>
```